Namecard Designs+Logo for a High End Automobile Company

We need a new business card for our company called Nordel Motorwerk.

www.nordelmotorwerk.example.sg
Our new website will be up in 2.5 months time.

We sell used and brand new continental cars like Valcrest, KTR, Almira, Dunvale and etc. Currently we are operating from 2 offices in Singapore and United Kingdom.

We want a design which is serious. We are open to colours but try to keep it at a maximum of 3 colours.

We prefer something simple and minimal. We are open to 2 sides printing or even 2 sided namecards. Both UK and Singapore company offices address must be in; either side by side, front and back, or even 2 sided cards.

The logo can be a text logo, emblem, abstract, pictorial or combination.

We are printing with Printlyx.com so please kindly follow the printing guideline.

http://uk.printlyx.example/help/faq/templates-and-guidelines.html

Rich and Car Enthusiasts

Printing

• Our 2 offices; UK and Singapore.

Our slogan which is " The Automobile Specialist"
• Not more than 3 colours

```html
<!DOCTYPE html>
<html lang="en">
<head>
<meta charset="utf-8">
<title>Nordel Motorwerk – Business Card</title>
<link href="https://fonts.googleapis.com/css2?family=Mulish:wght@700&family=Questrial&display=swap" rel="stylesheet">
<style>
  :root {
    --card-red: #b8262e;
    --ink-white: #ffffff;
    --page-bg: #ffffff;
  }
  html, body {
    margin: 0;
    padding: 0;
    overflow: hidden;
    background: var(--page-bg);
  }
  .canvas {
    position: relative;
    width: 1200px;
    height: 850px;
    overflow: hidden;
    background: var(--page-bg);
  }
  .card {
    position: absolute;
    width: 624px;
    height: 368px;
    border-radius: 36px;
    background: var(--card-red);
    color: var(--ink-white);
    overflow: hidden;
  }
  .card--front { left: 281px; top: 45px; }
  .card--back  { left: 285px; top: 440px; }

  .brand-dot {
    position: absolute;
    border: 4px solid var(--ink-white);
    border-radius: 50%;
    box-sizing: border-box;
  }
  .card--front .brand-dot { width: 140px; height: 140px; left: 242px; top: 108px; }
  .card--back  .brand-dot { width: 90px;  height: 90px;  left: 78px;  top: 70px; }

  .brand-name {
    position: absolute;
    margin: 0;
    font-family: "Mulish", sans-serif;
    font-weight: 700;
    letter-spacing: -0.5px;
    white-space: nowrap;
    transform: translateX(-50%);
    line-height: 1;
  }
  .brand-tagline {
    position: absolute;
    margin: 0;
    font-family: "Questrial", sans-serif;
    white-space: nowrap;
    transform: translateX(-50%);
    line-height: 1;
  }
  .card--front .brand-name    { left: 312px; top: 278px; font-size: 34px; }
  .card--front .brand-tagline { left: 312px; top: 313px; font-size: 15px; }
  .card--back  .brand-name    { left: 123px; top: 186px; font-size: 20px; }
  .card--back  .brand-tagline { left: 123px; top: 207px; font-size: 9.5px; }

  .contact {
    font-family: "Questrial", sans-serif;
    color: var(--ink-white);
  }
  .contact__company {
    position: absolute;
    left: 415px;
    top: 55px;
    margin: 0;
    font-size: 18px;
    font-weight: 400;
    transform: translateX(-50%);
    white-space: nowrap;
  }
  .office {
    position: absolute;
    font-size: 12px;
    line-height: 16px;
    letter-spacing: -0.2px;
  }
  .office__label {
    position: absolute;
    right: 212px;
    top: 0;
    white-space: nowrap;
  }
  .office__address {
    position: absolute;
    left: 418px;
    top: 0;
    margin: 0;
    font-style: normal;
    white-space: nowrap;
  }
  .office--sg { top: 100px; left: 0; width: 624px; }
  .office--sg .office__label { font-size: 12px; }
  .office--uk { top: 158px; left: 0; width: 624px; }
  .office--uk .office__label { font-size: 14px; }
  .office__address .line { display: block; }
  .office--sg .line--indent { padding-left: 0; }

  .contact-line {
    position: absolute;
    left: 383px;
    display: flex;
    align-items: center;
    font-size: 13px;
    white-space: nowrap;
  }
  .contact-line svg { width: 22px; height: 16px; margin-right: 13px; }
  .contact-line--phone { top: 225px; }
  .contact-line--email { top: 263px; }
</style>
</head>
<body>
<main class="canvas">

  <section class="card card--front" aria-label="Card front">
    <span class="brand-dot" aria-hidden="true"></span>
    <h1 class="brand-name">Nordel Motorwerk</h1>
    <p class="brand-tagline">European Automobile Specialist</p>
  </section>

  <section class="card card--back" aria-label="Card back">
    <span class="brand-dot" aria-hidden="true"></span>
    <p class="brand-name">Nordel Motorwerk</p>
    <p class="brand-tagline">European Automobile Specialist</p>

    <div class="contact">
      <h2 class="contact__company">Nordel Motorwerk</h2>

      <div class="office office--sg">
        <span class="office__label">Singapore:</span>
        <address class="office__address">
          <span class="line">8 Harbourfront Lane, One Harbourfront</span>
          <span class="line">Singapore 098631</span>
        </address>
      </div>

      <div class="office office--uk">
        <span class="office__label">UK:</span>
        <address class="office__address">
          <span class="line">12 Heron Reach, UK England</span>
          <span class="line">county</span>
        </address>
      </div>

      <div class="contact-line contact-line--phone">
        <svg viewBox="0 0 22 16" aria-hidden="true">
          <path d="M1 5 Q11 -1 21 5 L19 7.5 L15.5 6 L15.5 4.5 Q11 3 6.5 4.5 L6.5 6 L3 7.5 Z" fill="#fff"/>
          <path d="M6 7 L16 7 L19 15 L3 15 Z" fill="#fff"/>
          <circle cx="11" cy="11" r="2.3" fill="#b8262e"/>
        </svg>
        <span>0455 218 730</span>
      </div>

      <div class="contact-line contact-line--email">
        <svg viewBox="0 0 22 16" aria-hidden="true">
          <rect x="2" y="2.5" width="17" height="11" fill="none" stroke="#fff" stroke-width="1.3"/>
          <path d="M2 2.5 L10.5 9 L19 2.5 M2 13.5 L8 8 M19 13.5 L13 8" fill="none" stroke="#fff" stroke-width="1.3"/>
        </svg>
        <span>NordelMotorwerk@email.example</span>
      </div>
    </div>
  </section>

</main>
</body>
</html>
```